Marlow Estate Fixers (Handyman / Home Improvement Company)

Looking for a double sided professional looking business card with Logo attached to be highlighted on one side and throwing in an image of a handyman as an option would be nice to see as well. We are a company focused on providing quality Handyman and Home improvement services in a timely manner that is done right the first time with integrity

Industry/Entity Type

Handyman / Home Improvement

Contact Information for Business Card

(LOGO, Name, Mobile and office phone numbers, email) on front side of card, (the words "The SOLUTION to all of your Handyman and Home Improvement needs" followed by "Family Owned and Operated" at the very bottom) on the back.

Colors
EB3D1F
EC4F4E
F09395
F8D3D4
FCEDEE

Requirements
Must have
• Red, Gray, Black Color scheme
Should not have
• No Yellow or Blue colors

```html
<!DOCTYPE html>
<html lang="en">
<head>
<meta charset="utf-8">
<title>Marlow Estate Fixers – Business Card</title>
<link href="https://fonts.googleapis.com/css2?family=Montserrat:wght@400;500;600;800&display=swap" rel="stylesheet">
<style>
  :root{
    --bg:#1c1c1c;
    --card:#ffffff;
    --red:#e3262e;
    --ink:#1e1e1e;
    --rule:#8a8a8a;
    --white:#ffffff;
    --panel-line:#111111;
  }
  *{margin:0;padding:0;box-sizing:border-box}
  html,body{width:1200px;height:1059px;overflow:hidden;background:var(--bg)}
  body{position:relative;font-family:"Montserrat",sans-serif;color:var(--ink)}
  .card{position:absolute;left:261px;width:715px;height:408px;border-radius:24px;overflow:hidden}
  .card-front{top:95px;background:var(--card)}
  .card-back{top:530px}

  .brand{display:flex;align-items:center;gap:10px;font-family:"Montserrat",sans-serif;font-weight:800;color:var(--red);text-transform:uppercase;line-height:1.1;white-space:nowrap}
  .brand-mark{width:22px;height:22px;background:var(--red);flex:none}
  .card-front .brand{position:absolute;right:40px;top:78px;font-size:27px;text-align:right}

  .person-name{position:absolute;left:48px;top:190px;font-size:28px;font-weight:600;color:var(--red);line-height:1.2}
  .person-role{position:absolute;left:48px;top:236px;font-size:18px;font-weight:400;line-height:1.2}
  .divider{position:absolute;left:48px;top:266px;width:627px;height:1px;background:var(--rule)}

  .contact-list{position:absolute;left:42px;top:280px;list-style:none}
  .contact-list li{display:flex;align-items:center;gap:11px;height:29px;font-size:17px;white-space:nowrap}
  .contact-list .label{font-weight:600;color:var(--red);margin-right:2px}
  .contact-list svg{width:18px;height:18px;fill:var(--red);flex:none}
  .address{position:absolute;right:40px;top:338px;text-align:right;font-size:17px;line-height:29px;white-space:nowrap}

  .back-photo{position:absolute;inset:0;background:linear-gradient(120deg,#df4a50 0%,#e65a5f 45%,#ee6b6d 100%)}
  .tagline{position:absolute;left:40px;top:44px;width:330px;font-size:24px;font-weight:600;line-height:1.3;color:var(--white)}
  .tagline strong{font-weight:800}
  .brand-panel{position:absolute;left:420px;top:200px;width:266px;height:84px;background:var(--white);border:4px solid var(--panel-line);display:flex;align-items:center;justify-content:center}
  .brand-panel .brand{font-size:22px;text-align:center}
  .family-note{position:absolute;left:0;right:0;bottom:26px;text-align:center;font-size:16px;font-weight:600;letter-spacing:3px;text-transform:uppercase;color:var(--white)}
</style>
</head>
<body>
  <section class="card card-front">
    <div class="brand"><span class="brand-mark"></span><span>Marlow Estate<br>Fixers</span></div>
    <h1 class="person-name">Daniel Hartley</h1>
    <p class="person-role">Owner</p>
    <div class="divider"></div>
    <ul class="contact-list">
      <li><svg viewBox="0 0 24 24"><path d="M6.6 10.8a15.1 15.1 0 0 0 6.6 6.6l2.2-2.2a1 1 0 0 1 1-.25 11.4 11.4 0 0 0 3.6.57 1 1 0 0 1 1 1V20a1 1 0 0 1-1 1A17 17 0 0 1 3 4a1 1 0 0 1 1-1h3.5a1 1 0 0 1 1 1c0 1.25.2 2.45.57 3.57a1 1 0 0 1-.25 1z"/></svg><span class="label">M</span>044-987 654 321</li>
      <li><svg viewBox="0 0 24 24"><path d="M6.6 10.8a15.1 15.1 0 0 0 6.6 6.6l2.2-2.2a1 1 0 0 1 1-.25 11.4 11.4 0 0 0 3.6.57 1 1 0 0 1 1 1V20a1 1 0 0 1-1 1A17 17 0 0 1 3 4a1 1 0 0 1 1-1h3.5a1 1 0 0 1 1 1c0 1.25.2 2.45.57 3.57a1 1 0 0 1-.25 1z"/></svg><span class="label">O</span>044-987 650 100</li>
      <li><svg viewBox="0 0 24 24"><path d="M2 5h20v2.2l-10 6.3L2 7.2z M2 9.5l10 6.3 10-6.3V19H2z"/></svg>hello@marlowfixers.com</li>
      <li><svg viewBox="0 0 24 24"><circle cx="12" cy="12" r="10"/></svg>www.marlowfixers.com</li>
    </ul>
    <p class="address">17, Harbour Lane Avenue<br>60231, Country name</p>
  </section>

  <section class="card card-back">
    <div class="back-photo" role="img" aria-label="Red-tinted photo of a handyman kneeling and drilling a board beside toolboxes"></div>
    <p class="tagline">The <strong>SOLUTION</strong> to all of your Handyman and Home Improvement needs</p>
    <div class="brand-panel"><div class="brand"><span class="brand-mark"></span><span>Marlow Estate<br>Fixers</span></div></div>
    <p class="family-note">Family Owned and Operated</p>
  </section>
</body>
</html>
```